Velmora Freightway Solutions Business cards

Would like a very unique design catchy but professional for business cards. Please use log provided.Marlon WellsCeo and Founder TransCon Logistix Solutions1-888-913-3225mwells@tlsolutionsus.comwww.tlsolutionsus.com

```html
<!DOCTYPE html>
<html lang="en">
<head>
<meta charset="utf-8">
<title>Velmora Freightway Solutions – Business Cards</title>
<link rel="stylesheet" href="https://fonts.googleapis.com/css2?family=Montserrat:wght@600;700&family=Lato:wght@400&display=swap">
<style>
  :root {
    --stage: #2c2c2c;
    --card-white: #ffffff;
    --brand-blue: #1469b4;
    --brand-red: #e21f2b;
    --ink: #1f1f1f;
    --ink-soft: #3a3a3a;
    --rule: #9a9a9a;
    --back-top: #d42335;
    --back-bottom: #1770bb;
  }
  html, body {
    margin: 0;
    padding: 0;
    width: 1200px;
    height: 1200px;
    overflow: hidden;
    background: var(--stage);
  }
  .canvas {
    position: relative;
    width: 1200px;
    height: 1200px;
  }
  .card {
    position: absolute;
    top: 310px;
    height: 594px;
    box-shadow: 0 4px 10px rgba(0,0,0,0.45);
  }
  .card-front {
    left: 234px;
    width: 364px;
    background: var(--card-white);
  }
  .card-back {
    left: 627px;
    width: 369px;
    background: linear-gradient(to bottom, var(--back-top) 0%, var(--back-top) 15%, #7a4a7a 50%, var(--back-bottom) 88%);
  }
  .company-name {
    position: absolute;
    left: 0;
    right: 0;
    text-align: center;
    font-family: "Montserrat", sans-serif;
    font-weight: 700;
    text-transform: uppercase;
    margin: 0;
    line-height: 1.2;
  }
  .card-front .company-name {
    top: 470px;
    top: 160px;
    color: var(--brand-blue);
    font-size: 21px;
    letter-spacing: 1px;
  }
  .company-name .sub {
    display: block;
    font-size: 14px;
    letter-spacing: 3px;
    margin-top: 4px;
  }
  .card-back .company-name {
    top: 462px;
    color: #ffffff;
    font-size: 22px;
    letter-spacing: 1px;
  }
  .person {
    position: absolute;
    top: 393px;
    left: 0;
    right: 0;
    text-align: center;
  }
  .person-name {
    margin: 0;
    font-family: "Montserrat", sans-serif;
    font-weight: 700;
    font-size: 21px;
    letter-spacing: 0.5px;
    line-height: 1.1;
  }
  .person-name .first { color: var(--brand-blue); }
  .person-name .last { color: var(--brand-red); }
  .person-role {
    margin: 2px 0 0;
    font-family: "Lato", sans-serif;
    font-size: 16px;
    color: var(--ink-soft);
  }
  .contact-icons {
    position: absolute;
    top: 455px;
    left: 87px;
    width: 190px;
    height: 24px;
  }
  .contact-list {
    position: absolute;
    top: 490px;
    left: 0;
    right: 0;
    margin: 0;
    padding: 0;
    list-style: none;
    text-align: center;
    font-family: "Lato", sans-serif;
    font-size: 17px;
    line-height: 21.5px;
    color: var(--ink);
  }
  .back-url {
    position: absolute;
    top: 528px;
    left: 0;
    right: 0;
    text-align: center;
    font-family: "Lato", sans-serif;
    font-size: 17px;
    color: #ffffff;
    margin: 0;
  }
</style>
</head>
<body>
<div class="canvas">
  <section class="card card-front">
    <h1 class="company-name">Velmora Freightway<span class="sub">Solutions</span></h1>

    <div class="person">
      <p class="person-name"><span class="first">DORIAN</span> <span class="last">PIKE</span></p>
      <p class="person-role">CEO and Founder</p>
    </div>

    <svg class="contact-icons" viewBox="0 0 190 24" aria-hidden="true">
      <line x1="0" y1="12" x2="53" y2="12" stroke="var(--rule)" stroke-width="1"/>
      <line x1="137" y1="12" x2="190" y2="12" stroke="var(--rule)" stroke-width="1"/>
      <circle cx="67" cy="12" r="11.5" fill="var(--brand-blue)"/>
      <circle cx="95" cy="12" r="11.5" fill="var(--brand-blue)"/>
      <circle cx="122" cy="12" r="11.5" fill="var(--brand-blue)"/>
      <path d="M61 9.5 Q67 5 73 9.5 L71.5 11.5 L69 10.5 L69 9.5 Q67 8.8 65 9.5 L65 10.5 L62.5 11.5 Z M62.5 12.5 H71.5 L72 17 H62 Z" fill="#fff"/>
      <rect x="89" y="8" width="12" height="8" fill="none" stroke="#fff" stroke-width="1.3"/>
      <polyline points="89,8 95,12.5 101,8" fill="none" stroke="#fff" stroke-width="1.3"/>
      <circle cx="122" cy="12" r="5.5" fill="none" stroke="#fff" stroke-width="1.3"/>
      <ellipse cx="122" cy="12" rx="2.3" ry="5.5" fill="none" stroke="#fff" stroke-width="1"/>
      <line x1="116.5" y1="12" x2="127.5" y2="12" stroke="#fff" stroke-width="1"/>
    </svg>

    <ul class="contact-list">
      <li>1-888-470-6158</li>
      <li>dpike@vfwayroutes.com</li>
      <li>www.vfwayroutes.com</li>
    </ul>
  </section>

  <section class="card card-back">
    <h2 class="company-name">Velmora Freightway<span class="sub">Solutions</span></h2>
    <p class="back-url">www.vfwayroutes.com</p>
  </section>
</div>
</body>
</html>
```